Tech business card design

We need an amazing business card design for our new business 'Pexla' a marketing tech startup based in Sydney, Australia. We provide an online marketplace for businesses to search and buy advertising media, connect with service providers and learn more about marketing. We wish to communicate 'cool tech', reliability and professionalism and design based around our logo.

Target Market(s)

Business Owners

Contact Information for Business Card

Name
Position
Email Address
Website
Phone Number

Font styles to use
Other font styles liked:
• Avenir & Avenir Next

Colors

Designer to choose colors to be used in the design.

```html
<!DOCTYPE html>
<html lang="en">
<head>
<meta charset="utf-8">
<title>Pexla Business Card</title>
<link rel="stylesheet" href="https://fonts.googleapis.com/css2?family=Nunito+Sans:wght@400;700;900&display=swap">
<style>
  :root {
    --page-bg: #f0f0f0;
    --navy: #141a3e;
    --navy-deep: #1a1f48;
    --teal: #6ab3c2;
    --teal-text: #5aa9b8;
    --ghost: #e3e4e8;
    --body-text: #3a3a3a;
    --white: #ffffff;
  }
  * { margin: 0; padding: 0; box-sizing: border-box; }
  html, body {
    width: 1200px; height: 900px; overflow: hidden;
    background: var(--page-bg);
    font-family: "Nunito Sans", "Avenir Next", Avenir, sans-serif;
  }
  .card {
    position: absolute; left: 298px; width: 604px; height: 345px;
    overflow: hidden;
    box-shadow: 0 6px 22px rgba(0,0,0,0.18);
  }
  .card--front { top: 84px; }
  .card--back { top: 473px; background: var(--white); }

  .front-backdrop {
    position: absolute; inset: 0;
    background:
      radial-gradient(ellipse 70% 75% at 95% 10%, var(--teal) 0%, rgba(106,179,194,0.55) 35%, rgba(106,179,194,0) 75%),
      radial-gradient(ellipse 60% 50% at 60% 75%, rgba(90,150,175,0.35) 0%, rgba(90,150,175,0) 70%),
      linear-gradient(160deg, #23305a 0%, var(--navy-deep) 55%, #131638 100%);
  }
  .front-wordmark {
    position: absolute; left: 0; right: 0; top: 100px;
    text-align: center;
    font-weight: 900; font-size: 100px; line-height: 1;
    letter-spacing: -1px;
    color: var(--white);
    padding-right: 12px;
  }
  .front-url {
    position: absolute; left: 0; right: 0; top: 204px;
    text-align: center;
    font-size: 15px; letter-spacing: 3px;
    color: var(--white);
  }

  .ghost-wordmark {
    position: absolute; left: 20px; top: -58px;
    font-weight: 900; font-size: 200px; line-height: 1;
    letter-spacing: -2px;
    color: var(--ghost);
  }
  .back-wordmark {
    position: absolute; left: 58px; top: 133px;
    font-weight: 900; font-size: 80px; line-height: 1;
    letter-spacing: -1px;
    color: var(--navy);
  }
  .contact-block { position: absolute; left: 332px; top: 104px; }
  .contact-name {
    font-weight: 700; font-size: 20px; line-height: 1;
    color: var(--navy); letter-spacing: 0.3px;
  }
  .contact-role {
    margin-top: 5px;
    font-size: 14px; color: var(--teal-text);
  }
  .contact-list { list-style: none; margin-top: 17px; }
  .contact-item {
    display: flex; align-items: center; gap: 8px;
    height: 25px;
    font-size: 16px; color: var(--body-text);
  }
  .contact-icon {
    width: 20px; height: 20px; border-radius: 50%;
    background: var(--navy);
    display: flex; align-items: center; justify-content: center;
    flex: none;
  }
</style>
</head>
<body>
  <section class="card card--front">
    <div class="front-backdrop" role="img" aria-label="Flowing dotted wave pattern on a navy to teal gradient"></div>
    <div class="front-wordmark">pexla</div>
    <div class="front-url">www.pexlamedia.com.au</div>
  </section>

  <section class="card card--back">
    <div class="ghost-wordmark" aria-hidden="true">pexla</div>
    <div class="back-wordmark">pexla</div>
    <div class="contact-block">
      <h1 class="contact-name">MARCUS DALE</h1>
      <p class="contact-role">Founder | Director</p>
      <ul class="contact-list">
        <li class="contact-item">
          <span class="contact-icon">
            <svg width="10" height="12" viewBox="0 0 10 12"><rect x="1.5" y="0.7" width="7" height="10.6" rx="1.2" fill="none" stroke="#fff" stroke-width="1.2"/><circle cx="5" cy="9.3" r="0.7" fill="#fff"/></svg>
          </span>
          +61 (0)400 555 019
        </li>
        <li class="contact-item">
          <span class="contact-icon">
            <svg width="11" height="8" viewBox="0 0 11 8"><rect x="0" y="0" width="11" height="8" fill="#fff"/><path d="M0 0 L5.5 4.5 L11 0" fill="none" stroke="#141a3e" stroke-width="1"/></svg>
          </span>
          marcus@pexlamedia.com.au
        </li>
        <li class="contact-item">
          <span class="contact-icon">
            <svg width="12" height="12" viewBox="0 0 12 12" fill="none" stroke="#fff" stroke-width="0.9"><circle cx="6" cy="6" r="5"/><ellipse cx="6" cy="6" rx="2.2" ry="5"/><path d="M1 6 H11 M2 3.2 H10 M2 8.8 H10"/></svg>
          </span>
          www.pexlamedia.com.au
        </li>
      </ul>
    </div>
  </section>
</body>
</html>
```